Sunset Harbor Living Web Page

We need a web page design that has two intro pages - first being a 'home page', then a link to the second page that has the 'content tabs' and a 'call to action' (see below).

The business helps people that wish to retire to S.E.Asia (Thailand, Malaysia, Indonesia,The Philippines etc) - to enjoy the lifestyle and the remaining years of their lives. What attracts S.E.Asia to many people is the lower cost, the atmoshpere and beauty of the tropics and the vibrancy of the various countries.

People that are wishing to make the most of their retirement and are adventurous at a great bargain compared to the cost of their own countries will be interested.

We help them achieve this - visa, financials (tax, gov't payments etc), introduce them to the right people for property, clubs, retirement facilities, insurance and so forth.

Therefore we are providing an extremely wide ranging service and this site will provide broad but general information only - with a call to action to come and see us for more specific information and how we can help them specifically.

This site will be predominantly for travel and lifestyle, it will be linked with another financial services (financial planning) site later down the track.

The colour scheme is dark green and blue - as per the attached logo design. Photos and background just think lifestyle and S.E.Asia - beaches/mountains/water/recreational activities for retirees.

Target market is mostly those coming up to retirement to those that are already retired. But we also expect to have some interest with younger people that would like to find out more and plan for the future. So a broad age group but I would say mostly 40-70 yrs old.

On the first (Home) page we would like our company name 'Sunset Harbor Living', our logo (which will be on all pages) and a statement such as: “Imagine a retirement where your dreams are brought to life, and you have never felt more alive. Let us show you how”. Then a link to the second page.

We would like an uncluttered site. On the second (contents) page the tabs would be:

- Visa
- Property
- Financials
- Travel
- Insurance & Healthcare
- Medical Tourism
- Cost of living
- Weekly Blogs and articles
- Sunset Harbor Living story

We would also like a call to action on the second page - asking them to leave their contact details if they wish to learn more or sign up to our weekly newsletter/blog.

We are open to suggestions and your imaginations.

Thank you
Malcolm

Font styles to use
Serif
Script

Colors
0255a3
3377b5
00a990
9bcb3c
abd036
33b8a4
85abd2
cadf82
86cfc6

Requirements
Must have
• I have been asked by the web designer to receive a 'Web Font' so that we can 'get off of Zentrofy'. Hope that makes sense.

```html
<!DOCTYPE html>
<html lang="en">
<head>
<meta charset="utf-8">
<title>Sunset Harbor Living</title>
<link rel="stylesheet" href="https://fonts.googleapis.com/css2?family=Abel&family=Montserrat:wght@700&family=Mulish:wght@700&display=swap">
<style>
  :root {
    --sky: #232a37;
    --sea-deep: #1c3a47;
    --sea: #24505a;
    --sand: #4b4a4b;
    --sand-dark: #3a393a;
    --brand-green: #0fb157;
    --brand-blue: #0b9ee0;
    --white: #ffffff;
    --text-soft: #e4e4e4;
  }
  * { margin: 0; padding: 0; box-sizing: border-box; }
  html, body { width: 1200px; height: 683px; overflow: hidden; background: var(--sky); }
  .hero {
    position: relative;
    width: 1200px;
    height: 683px;
    overflow: hidden;
  }
  .hero-backdrop {
    position: absolute;
    inset: 0;
    background: linear-gradient(180deg,
      var(--sky) 0%, #27303d 21%,
      var(--sea-deep) 22%, var(--sea) 33%,
      var(--sand) 34.5%, #504f50 60%, var(--sand-dark) 100%);
  }
  .hero-content {
    position: absolute;
    inset: 0;
    display: flex;
    flex-direction: column;
    align-items: center;
  }
  .brand-mark {
    margin-top: 148px;
    width: 104px;
    height: 104px;
    border-radius: 50%;
    background: var(--brand-green);
  }
  .brand-name {
    margin-top: 28px;
    font-family: 'Montserrat', sans-serif;
    font-weight: 700;
    font-size: 32px;
    letter-spacing: -0.5px;
    color: var(--white);
    line-height: 1;
  }
  .brand-tagline {
    margin-top: 6px;
    font-family: 'Montserrat', sans-serif;
    font-weight: 700;
    font-size: 11.5px;
    letter-spacing: 0.4px;
    color: var(--white);
  }
  .headline {
    margin-top: 28px;
    font-family: 'Abel', sans-serif;
    font-weight: 400;
    font-size: 35px;
    line-height: 49px;
    text-align: center;
    color: var(--text-soft);
    text-shadow: 0 1px 3px rgba(0,0,0,0.4);
  }
  .cta-button {
    margin-top: 24px;
    position: relative;
    display: flex;
    align-items: center;
    width: 333px;
    height: 56px;
    border: 2px solid var(--white);
    border-radius: 6px;
    background: var(--brand-green);
    overflow: hidden;
    text-decoration: none;
  }
  .cta-label {
    padding-left: 32px;
    font-family: 'Mulish', sans-serif;
    font-weight: 700;
    font-size: 20px;
    color: var(--white);
  }
  .cta-icon {
    position: absolute;
    right: -2px;
    top: -2px;
    width: 58px;
    height: 56px;
  }
</style>
</head>
<body>
  <main class="hero">
    <div class="hero-backdrop" role="img" aria-label="Dimmed photo of colourful wooden beach chairs lined up on white sand facing a calm tropical sea at dusk"></div>
    <div class="hero-content">
      <div class="brand-mark" aria-hidden="true"></div>
      <h1 class="brand-name">Sunset Harbor Living</h1>
      <p class="brand-tagline">DREAM LIFESTYLE SPECIALISTS</p>
      <p class="headline">Imagine A Retirement Where Your Dreams Are Brought To Life,<br>&amp; You Have Never Felt More Alive</p>
      <a class="cta-button" href="#contents">
        <span class="cta-label">Let Us Show You How</span>
        <svg class="cta-icon" viewBox="0 0 58 56" aria-hidden="true">
          <circle cx="44" cy="28" r="36" fill="var(--brand-blue)" stroke="var(--white)" stroke-width="2"/>
          <path d="M21 18 L30 28 L21 38 M29 18 L38 28 L29 38" fill="none" stroke="var(--white)" stroke-width="2" stroke-linecap="round" stroke-linejoin="round"/>
        </svg>
      </a>
    </div>
  </main>
</body>
</html>
```